Brookmere Osteopathy flyer

I want a clean clear DL flyer (but also want an A4 poster) promoting a new Osteopathic business in a semi rural area in Tasmania (Australia).
It can have pictures like the examples attached to show people what Osteopathy is (its like Chiropractic and physiotherapy).
I am the sole practioner and am male, so any pictures would be best to be a white male if possible.
I've attached some wording, you can use all, or none of it
I don't have a phone number for the business yet
info@brookmereosteopathy.example
www.brookmereosteopathy.example
Target Market(s)
Australians, from tradies, professionals, babies to retired people
Industry/Entity Type
Health
Look and feel

```html
<!DOCTYPE html>
<html lang="en">
<head>
<meta charset="utf-8">
<title>Brookmere Osteopathy – DL Flyer</title>
<link href="https://fonts.googleapis.com/css2?family=Poppins:wght@300;400;500;600;700;800&family=Allura&display=swap" rel="stylesheet">
<style>
  :root {
    --blue: #0a7cc4;
    --blue-deep: #066aaf;
    --blue-light: #1494d6;
    --orange: #f39332;
    --orange-deep: #ee7d22;
    --ink: #3a3a3a;
    --rule: #c9c9c9;
    --white: #ffffff;
    --backdrop: #c4c4c4;
  }
  * { box-sizing: border-box; margin: 0; padding: 0; }
  html, body { width: 1125px; height: 1200px; overflow: hidden; }
  body { background: var(--backdrop); font-family: "Poppins", sans-serif; position: relative; }

  .flyer { position: absolute; top: 135px; width: 439px; height: 930px; overflow: hidden; box-shadow: 0 18px 30px rgba(0,0,0,.25); }
  .flyer--front { left: 102px; background: var(--white); }
  .flyer--back { left: 584px; background: var(--white); }
  .abs { position: absolute; }

  /* FRONT */
  .front-band { left: 0; top: 499px; width: 100%; height: 431px; background: linear-gradient(180deg, var(--blue) 0%, var(--blue-deep) 100%); }
  .corner-ring { right: -40px; top: -40px; width: 105px; height: 105px; border-radius: 50%; border: 2px solid var(--blue-light); }
  .corner-dot { right: -36px; top: -36px; width: 88px; height: 88px; border-radius: 50%; background: var(--blue-light); }
  .brand-mark { left: 155px; top: 37px; width: 128px; height: 128px; border-radius: 50%; border: 2px solid var(--blue-light);
    display: flex; align-items: center; justify-content: center; text-align: center; }
  .brand-name { font-weight: 600; font-size: 14px; line-height: 18px; color: var(--blue); letter-spacing: .3px; }
  .sun-art { left: -20px; top: 300px; width: 82px; height: 140px; border-radius: 0 70px 70px 0; background: radial-gradient(circle at 0 50%, var(--orange) 0 30%, rgba(243,147,50,.25) 31% 100%); }

  .headline { left: 0; width: 439px; text-align: center; }
  .headline-top { top: 178px; font-size: 41px; line-height: 1; color: var(--ink); font-weight: 300; letter-spacing: -1px; }
  .headline-top b { font-weight: 700; }
  .headline-main { top: 214px; font-size: 61px; line-height: 1; font-weight: 800; color: var(--orange); letter-spacing: -1px; }
  .headline-script { top: 258px; left: 20px; font-family: "Allura", cursive; font-size: 84px; color: var(--blue); line-height: 1; }

  .hero-ring { left: 54px; top: 354px; }
  .hero-photo { left: 91px; top: 391px; width: 256px; height: 256px; border-radius: 50%; border: 6px solid var(--white); background: linear-gradient(135deg, #4d8fc4 0%, #c9a58e 55%, #6e6e6e 100%); }
  .detail-photo { left: 230px; top: 603px; width: 152px; height: 152px; border-radius: 50%; border: 11px solid var(--white); background: linear-gradient(135deg, #9cc7e6 0%, #d8cfc6 60%, #555 100%); box-shadow: 0 8px 14px rgba(0,0,0,.25); }

  .care-copy { left: 70px; top: 690px; color: var(--white); font-size: 15px; line-height: 18px; }
  .care-copy strong { display: block; font-weight: 700; }
  .care-copy span { display: block; font-weight: 400; font-size: 15px; }

  .front-rule { left: 45px; top: 790px; width: 350px; height: 1px; background: rgba(255,255,255,.5); }
  .front-phone { left: 45px; top: 803px; display: flex; align-items: center; gap: 6px; color: var(--white); font-weight: 800; font-size: 39px; letter-spacing: .5px; }
  .phone-dot { width: 32px; height: 32px; border-radius: 50%; background: var(--orange); display: flex; align-items: center; justify-content: center; }

  .url-pill { left: 48px; width: 343px; height: 34px; border-radius: 17px; background: var(--orange); color: var(--white); font-size: 14px; letter-spacing: 1.6px; display: flex; align-items: center; justify-content: center; border: 1.5px solid var(--white); white-space: nowrap; }
  .url-pill b { font-weight: 700; }
  .flyer--front .url-pill { top: 852px; }

  /* BACK */
  .back-band { left: 0; top: 0; width: 100%; height: 589px; background: linear-gradient(180deg, var(--blue-deep) 0%, var(--blue) 100%); }
  .reasons-card { left: 43px; top: 42px; width: 351px; height: 440px; background: var(--white); border-radius: 26px; padding: 31px 44px 0 33px; }
  .reasons-title { font-size: 21px; line-height: 25px; font-weight: 600; color: var(--ink); margin-bottom: 14px; }
  .reasons-title em { font-style: normal; color: var(--blue-light); display: block; }
  .reasons-list { list-style: none; }
  .reasons-list li { display: flex; align-items: center; gap: 6px; height: 33px; font-size: 13px; color: #222; border-bottom: 1px solid var(--rule); white-space: nowrap; }
  .reasons-list li:last-child { border-bottom: none; }
  .reason-icon { width: 26px; height: 26px; border-radius: 50%; flex: none; display: flex; align-items: center; justify-content: center; }
  .reason-icon--blue { background: var(--blue-light); }
  .reason-icon--orange { background: var(--orange); }
  .reason-icon i { width: 8px; height: 12px; border-radius: 4px; background: var(--white); }

  .treat-photo { top: 516px; width: 120px; height: 120px; border-radius: 50%; border: 4px solid var(--white); box-shadow: 0 6px 10px rgba(0,0,0,.2); }
  .treat-photo--1 { left: 44px; background: linear-gradient(135deg, #d6b39a, #8d6b57); }
  .treat-photo--2 { left: 154px; background: linear-gradient(135deg, #e8e8e8, #2f6f73); }
  .treat-photo--3 { left: 270px; background: linear-gradient(135deg, #f2f2f2, #b79b86); }

  .method-copy { left: 20px; top: 677px; width: 399px; text-align: center; font-size: 13px; line-height: 15px; color: var(--ink); }
  .method-copy strong { display: block; font-weight: 600; font-size: 12.8px; white-space: nowrap; }
  .back-rule { left: 43px; top: 755px; width: 351px; height: 1px; background: #888; }
  .map-art { left: 57px; top: 769px; width: 80px; height: 72px; border-radius: 12px; background: linear-gradient(135deg, #f1f1f1, #d9d9d9); }
  .contact { left: 156px; }
  .contact-phone { top: 769px; font-size: 22px; font-weight: 800; color: var(--ink); display: flex; align-items: center; gap: 3px; }
  .contact-line { font-size: 12px; font-weight: 500; color: var(--ink); display: flex; align-items: center; gap: 7px; white-space: nowrap; }
  .contact-line--email { top: 800px; }
  .contact-line--addr { top: 822px; }
  .mini-dot { width: 14px; height: 14px; border-radius: 50%; background: var(--orange); flex: none; }
  .flyer--back .url-pill { top: 852px; }
</style>
</head>
<body>

<section class="flyer flyer--front">
  <div class="abs front-band"></div>
  <div class="abs corner-ring"></div>
  <div class="abs corner-dot"></div>

  <div class="abs brand-mark">
    <span class="brand-name">Brookmere<br>Osteopathy</span>
  </div>

  <div class="abs sun-art" role="img" aria-label="Decorative rising sun with rays"></div>

  <div class="abs headline headline-top">YOUR <b>BODY</b></div>
  <div class="abs headline headline-main">DESERVES</div>
  <div class="abs headline headline-script">Relief</div>

  <svg class="abs hero-ring" width="330" height="330" viewBox="0 0 330 330" aria-hidden="true">
    <path d="M165 16 A149 149 0 1 1 120 307" fill="none" stroke="var(--orange)" stroke-width="30"/>
    <path d="M165 16 A149 149 0 0 0 120 307" fill="none" stroke="var(--orange-deep)" stroke-width="30" opacity=".9"/>
  </svg>
  <div class="abs hero-photo" role="img" aria-label="Osteopath treating a woman's shoulder"></div>
  <div class="abs detail-photo" role="img" aria-label="Practitioner working on a patient's back on a treatment table"></div>

  <div class="abs care-copy">
    <strong>PROFESSIONAL<br>OSTEOPATHIC CARE</strong>
    <span>For pain, tension, and<br>everyday discomfort</span>
  </div>

  <div class="abs front-rule"></div>
  <div class="abs front-phone">
    <span class="phone-dot">
      <svg width="18" height="18" viewBox="0 0 24 24"><path fill="#fff" d="M6.6 10.8a15 15 0 0 0 6.6 6.6l2.2-2.2c.3-.3.7-.4 1-.2 1.1.4 2.3.6 3.6.6.6 0 1 .4 1 1V20c0 .6-.4 1-1 1A17 17 0 0 1 3 4c0-.6.4-1 1-1h3.5c.6 0 1 .4 1 1 0 1.3.2 2.5.6 3.6.1.3 0 .7-.2 1z"/></svg>
    </span>
    03 6100 2040
  </div>
  <div class="abs url-pill">www.<b>brookmereosteopathy</b>.example</div>
</section>

<section class="flyer flyer--back">
  <div class="abs back-band"></div>

  <div class="abs reasons-card">
    <h2 class="reasons-title">Common reasons people <em>visit an osteopath</em></h2>
    <ul class="reasons-list">
      <li><span class="reason-icon reason-icon--blue"><i></i></span>Back / neck pain</li>
      <li><span class="reason-icon reason-icon--orange"><i></i></span>Headaches / migraines</li>
      <li><span class="reason-icon reason-icon--blue"><i></i></span>Joint and muscle pain</li>
      <li><span class="reason-icon reason-icon--orange"><i></i></span>Pregnancy-related discomfort</li>
      <li><span class="reason-icon reason-icon--blue"><i></i></span>Disc related issues</li>
      <li><span class="reason-icon reason-icon--orange"><i></i></span>Sciatica</li>
      <li><span class="reason-icon reason-icon--blue"><i></i></span>Plantar fasciitis</li>
      <li><span class="reason-icon reason-icon--orange"><i></i></span>Tendonitis / Bursitis</li>
      <li><span class="reason-icon reason-icon--blue"><i></i></span>Adhesive capsulitis (frozen shoulder)</li>
      <li><span class="reason-icon reason-icon--orange"><i></i></span>Tennis / Golfers elbow</li>
    </ul>
  </div>

  <div class="abs treat-photo treat-photo--1" role="img" aria-label="Hands massaging a patient's back"></div>
  <div class="abs treat-photo treat-photo--2" role="img" aria-label="Practitioner stretching a patient's leg"></div>
  <div class="abs treat-photo treat-photo--3" role="img" aria-label="Shoulder treatment on a lying patient"></div>

  <p class="abs method-copy">Osteopaths use a combination of
    <strong>joint manipulation, targeted deep tissue massage<br>and stretching to improve function, relieve pain<br>and support the body’s ability to heal itself.</strong>
  </p>

  <div class="abs back-rule"></div>
  <div class="abs map-art" role="img" aria-label="Outline map of Australia with Tasmania highlighted"></div>

  <div class="abs contact contact-phone">
    <svg width="18" height="18" viewBox="0 0 24 24"><circle cx="12" cy="12" r="12" fill="var(--orange)"/><path fill="#fff" d="M8.6 11a8 8 0 0 0 4.4 4.4l1.4-1.4c.2-.2.5-.3.7-.1.7.2 1.5.4 2.3.4.4 0 .6.3.6.6V17c0 .4-.3.6-.6.6A10.6 10.6 0 0 1 6.4 7c0-.4.3-.6.6-.6h2.2c.4 0 .6.3.6.6 0 .8.1 1.6.4 2.3 0 .2 0 .5-.2.7z"/></svg>
    03 6100 2040
  </div>
  <div class="abs contact contact-line contact-line--email"><span class="mini-dot"></span>info@brookmereosteopathy.example</div>
  <div class="abs contact contact-line contact-line--addr"><span class="mini-dot"></span>24 Ridge Lane, Brookmere</div>

  <div class="abs url-pill">www.<b>brookmereosteopathy</b>.example</div>
</section>

</body>
</html>
```